Vornel Wellness Business Card

A Double Sided Business Card

I am a private company in Melbourne, Australia, working in the Health industry. I am a nutritionist and lifestyle coach, whom specialises in using raw foods ie. fruits/nuts/vegetables to help heal my clients and enable them to achieve their ultimate state of health.

I want a sophisticated design and colour for my card that appeals to both men and women from teenage through to elderly.

Front of Card:

Red apple peel spiral in the shape of an apple. I would like a leaf/leaves coming off the stem of the apple. Please see attachments for example.

***On Right Hand side of Image is business Name: Vornel Wellness

Underneath LOGO use slogan " Let Food Be Your Medicine"

***Use Deep Red and Blues for Text Colouring

Back of Card:

Marisol Dekkert
Nutritional Specialist and Lifestyle Coach

Specialising in: Diseased Conditions
Weight Management
Achieving your Ultimate State of Health

enquiries@vornelwellness.com.au 0457 396 504

**Make sure the front design of the card flows onto the back.
Updates

Email address has been amended, Also more specific details have been given for apple peel Image, and another image attached as example of Leaf on stem of apple.

I little more insight into what sort of feel were trying to create. We're apart of the health industry, and we want the card to have a medical/clinical feeling about it.

Target Market(s)

Males and Females from teenages to elderly

Industry/Entity Type

Business

Requirements
Must have
• Red Apple Peel Spiral, in the shape of an apple, with a leaf/leaves attached to stem.
***Must be in the shape of an apple
***Please use coloring on inside of apple peel to resemble inside of an apple.
Nice to have
• I would like my card to have a clinical feel.
Should not have
• We don't want the image of the apple to look like a Christmas decoration

```html
<!DOCTYPE html>
<html lang="en">
<head>
<meta charset="utf-8">
<title>Vornel Wellness Business Card</title>
<link rel="stylesheet" href="https://fonts.googleapis.com/css2?family=Quicksand:wght@400;500;600;700&display=swap">
<style>
  :root {
    --page-bg: #ecebe8;
    --card-light: #fbfbfb;
    --card-mid: #e4e4e4;
    --swoosh-grey: #cfcfcf;
    --swoosh-dark: #b9b9b9;
    --deep-red: #d3242a;
    --deep-blue: #2d3e93;
    --text-grey: #8d8d8d;
    --text-dark: #1f1f2e;
    --white: #ffffff;
  }
  * { margin: 0; padding: 0; box-sizing: border-box; }
  html, body {
    width: 1200px; height: 900px; overflow: hidden;
    background: var(--page-bg);
    font-family: "Quicksand", sans-serif;
  }
  .canvas { position: relative; width: 1200px; height: 900px; }
  .card {
    position: absolute; width: 630px; height: 400px; overflow: hidden;
    background: linear-gradient(180deg, var(--card-light) 0%, var(--card-mid) 100%);
    box-shadow: 0 6px 18px rgba(0,0,0,0.18);
  }
  .card-back { left: 40px; top: 50px; }
  .card-front { left: 530px; top: 450px; }
  .swooshes { position: absolute; inset: 0; width: 100%; height: 100%; }

  .back-content { position: absolute; inset: 0; }
  .person-name {
    position: absolute; left: 0; right: 0; top: 118px; text-align: center;
    color: var(--deep-red); font-size: 33px; font-weight: 500; line-height: 40px;
  }
  .person-role {
    position: absolute; left: 0; right: 0; top: 160px; text-align: center;
    color: var(--text-grey); font-size: 20px; font-weight: 500; line-height: 22px;
  }
  .specialties { position: absolute; left: 0; right: 0; top: 218px; text-align: center; }
  .specialties-title { color: var(--deep-blue); font-size: 22px; font-weight: 600; line-height: 28px; }
  .specialties-list { color: var(--text-dark); font-size: 18px; font-weight: 500; line-height: 24px; }
  .contact { position: absolute; left: 60px; bottom: 18px; color: var(--white); font-size: 19px; font-weight: 500; }
  .contact-row { display: flex; align-items: center; gap: 8px; height: 30px; }
  .contact-icon { width: 22px; height: 22px; }
  .mark-small {
    position: absolute; right: 26px; bottom: 26px; display: flex; align-items: center; gap: 6px;
    color: var(--deep-red); font-size: 13px; font-weight: 700;
  }
  .mark-dot { width: 26px; height: 26px; border-radius: 50%; background: var(--deep-red); }

  .front-content { position: absolute; left: 90px; top: 120px; display: flex; align-items: center; gap: 18px; }
  .mark-circle { width: 110px; height: 110px; border-radius: 50%; background: var(--deep-red); }
  .brand-name { color: var(--deep-red); font-size: 44px; font-weight: 700; line-height: 48px; }
  .brand-slogan { color: var(--deep-blue); font-size: 21px; font-weight: 600; margin-top: 4px; }
</style>
</head>
<body>
<main class="canvas">

  <section class="card card-back" aria-label="Card back">
    <svg class="swooshes" viewBox="0 0 630 400" preserveAspectRatio="none" aria-hidden="true">
      <path d="M0 90 C160 30 420 10 630 50 L630 105 C420 70 180 95 0 150 Z" fill="var(--swoosh-grey)" opacity="0.6"/>
      <path d="M0 150 C200 95 430 80 630 115 L630 170 C430 145 200 175 0 220 Z" fill="var(--white)" opacity="0.8"/>
      <path d="M0 310 C180 315 420 310 630 250 L630 400 L0 400 Z" fill="var(--swoosh-dark)"/>
      <path d="M0 330 C200 340 430 330 630 285 L630 400 L0 400 Z" fill="var(--swoosh-grey)" opacity="0.5"/>
    </svg>
    <div class="back-content">
      <h1 class="person-name">Marisol Dekkert</h1>
      <p class="person-role">Nutritional Specialist<br>Lifestyle Coach</p>
      <div class="specialties">
        <h2 class="specialties-title">Specialising in:</h2>
        <p class="specialties-list">·Diseased Conditions &nbsp;·Weight Management<br>·Achieving your Ultimate State of Health</p>
      </div>
      <div class="contact">
        <div class="contact-row">
          <svg class="contact-icon" viewBox="0 0 22 22" aria-hidden="true">
            <circle cx="11" cy="11" r="11" fill="var(--deep-red)"/>
            <circle cx="11" cy="11" r="6" fill="none" stroke="var(--white)" stroke-width="1.4"/>
            <path d="M5 11 H17 M11 5 C8 8 8 14 11 17 M11 5 C14 8 14 14 11 17" fill="none" stroke="var(--white)" stroke-width="1.2"/>
          </svg>
          <span>enquiries@vornelwellness.com.au</span>
        </div>
        <div class="contact-row">
          <svg class="contact-icon" viewBox="0 0 22 22" aria-hidden="true">
            <circle cx="11" cy="11" r="11" fill="var(--deep-red)"/>
            <path d="M7.5 5.5 L9.5 5 L10.5 8 L9 9.2 C9.7 10.8 11.2 12.3 12.8 13 L14 11.5 L17 12.5 L16.5 14.5 C11.5 15.5 6.5 10.5 7.5 5.5 Z" fill="var(--white)"/>
          </svg>
          <span>0457 396 504</span>
        </div>
      </div>
      <div class="mark-small">
        <span class="mark-dot"></span>
        <span>Vornel Wellness</span>
      </div>
    </div>
  </section>

  <section class="card card-front" aria-label="Card front">
    <svg class="swooshes" viewBox="0 0 630 400" preserveAspectRatio="none" aria-hidden="true">
      <path d="M0 90 C180 40 430 40 630 70 L630 110 C430 80 200 90 0 140 Z" fill="var(--swoosh-grey)" opacity="0.35"/>
      <path d="M0 250 C200 220 430 240 630 210 L630 400 L0 400 Z" fill="var(--swoosh-grey)"/>
      <path d="M0 280 C200 270 430 290 630 260 L630 400 L0 400 Z" fill="var(--card-mid)"/>
    </svg>
    <div class="front-content">
      <span class="mark-circle"></span>
      <div class="brand">
        <p class="brand-name">Vornel Wellness</p>
        <p class="brand-slogan">Let Food Be Your Medicine</p>
      </div>
    </div>
  </section>

</main>
</body>
</html>
```